Business Card design for law firm = Brightvale Australia

We are seeking a new design for our business cards.
We are keeping our logo, which is attached.
We need space for
Name
Title
Address is , which is
Level 7
214 Marlowe Street
Sydney NSW 2047
Phone :
Mobile :
Fax :
Email :
DX :
website www.brightvale-example.com.au

Industry/Entity Type

Law Firm / Banking and Finance

Contact Information for Business Card

We are seeking a new design for our business cards. We are keeping our logo. We need space for Name Title Address is Level 7 214 Marlowe Street Sydney NSW 2047 Phone Mobile Fax Email DX website www.brightvale-example.com.au

Colors
0054AA
0677BA
7BADD7
CADEEF
E8F1F8

Requirements
Must have
• see our website for general feel www.brightvale-example.com.au

```html
<!DOCTYPE html>
<html lang="en">
<head>
<meta charset="utf-8">
<title>Brightvale Australia — Business Card</title>
<link href="https://fonts.googleapis.com/css2?family=Crimson+Text:wght@400&family=Open+Sans:wght@400&display=swap" rel="stylesheet">
<style>
  :root {
    --backdrop: #2b2b2b;
    --paper-light: #f4f4f4;
    --paper-shade: #dcdcdc;
    --navy: #2a479b;
    --cyan: #0a8cc4;
    --ink: #2a2a2a;
  }
  * { margin: 0; padding: 0; box-sizing: border-box; }
  html, body { width: 1200px; height: 1138px; overflow: hidden; }
  body { background: var(--backdrop); position: relative; font-family: "Crimson Text", Georgia, serif; }

  .card {
    position: absolute;
    width: 620px; height: 374px;
    border-radius: 15px;
    overflow: hidden;
    background: linear-gradient(160deg, var(--paper-light) 0%, #ececec 55%, var(--paper-shade) 100%);
  }
  .card--front { left: 272px; top: 184px; }
  .card--back  { left: 274px; top: 606px; }

  /* Front */
  .front-name {
    position: absolute; left: 0; width: 100%; top: 160px;
    text-align: center; font-size: 60px; line-height: 1; color: var(--navy);
  }
  .front-tagline {
    position: absolute; left: 0; width: 100%; top: 234px;
    text-align: center; font-family: "Open Sans", Arial, sans-serif;
    font-size: 19px; letter-spacing: 2px; color: var(--cyan);
  }
  .front-web {
    position: absolute; left: 0; width: 100%; top: 330px;
    text-align: center; font-size: 15px; letter-spacing: 6px; color: var(--ink);
  }
  .front-band {
    position: absolute; left: 142px; width: 340px; bottom: 0; height: 9px;
    background: var(--navy);
  }

  /* Back */
  .back-name {
    position: absolute; left: 60px; top: 192px;
    font-size: 48px; line-height: 1; color: var(--navy);
  }
  .back-tagline {
    position: absolute; left: 60px; top: 247px;
    font-family: "Open Sans", Arial, sans-serif;
    font-size: 15px; letter-spacing: 1.5px; color: var(--cyan);
  }

  .contact { position: absolute; left: 346px; top: 88px; color: var(--ink); }
  .contact__person { font-size: 29px; line-height: 1; color: var(--navy); }
  .contact__title { font-size: 16px; line-height: 20px; }
  .contact__address { margin-top: 14px; font-size: 16px; line-height: 20px; }
  .contact__list { list-style: none; margin-top: 10px; font-size: 16px; line-height: 20px; }
  .contact__list li { display: flex; align-items: center; }
  .contact__list svg { width: 13px; height: 13px; margin: 0 15px 0 2px; fill: var(--cyan); flex: none; }
</style>
</head>
<body>

<section class="card card--front" aria-label="Business card front">
  <div class="front-name">Brightvale</div>
  <div class="front-tagline">banking and finance law</div>
  <div class="front-web">www.brightvale-example.com.au</div>
  <div class="front-band"></div>
</section>

<section class="card card--back" aria-label="Business card back">
  <div class="back-name">Brightvale</div>
  <div class="back-tagline">banking and finance law</div>

  <div class="contact">
    <div class="contact__person">Sam Whitford</div>
    <div class="contact__title">Managing Director</div>
    <div class="contact__address">Level 7 214 Marlowe St<br>Sydney NSW 2047</div>
    <ul class="contact__list">
      <li>
        <svg viewBox="0 0 16 16" aria-hidden="true"><path d="M1 5c0-2 3-3 7-3s7 1 7 3v1h-3V5H4v1H1z"/><path d="M3 8l2-2h6l2 2v6H3z"/></svg>
        02 9000 0147
      </li>
      <li>
        <svg viewBox="0 0 16 16" aria-hidden="true"><rect x="4" y="1" width="8" height="4"/><rect x="1" y="6" width="14" height="6" rx="1"/><rect x="4" y="10" width="8" height="5"/></svg>
        02 9000 0148
      </li>
      <li>
        <svg viewBox="0 0 16 16" aria-hidden="true"><path d="M1 3h14v10H1z M2 4l6 5 6-5" stroke="#fff" stroke-width="1"/></svg>
        sam@brightvale-example.com.au
      </li>
      <li>
        <svg viewBox="0 0 16 16" aria-hidden="true"><circle cx="8" cy="8" r="7"/><path d="M1 8h14M8 1v14M3 4h10M3 12h10" stroke="#fff" stroke-width="0.8" fill="none"/></svg>
        www.brightvale-example.com.au
      </li>
    </ul>
  </div>
</section>

</body>
</html>
```